Harborline Auto LLC

Car Dealer Customer Service
Address: 2874 Cresthaven Road, Shelbyville, TN 37162
web: www.harborlineautoxq.net
email: harborlineautoxq@mailnest.example
Phone: (931) 555-0148
Phone: (629) 555-0173

```html
<!DOCTYPE html>
<html lang="en">
<head>
<meta charset="utf-8">
<title>Harborline Auto – Business Card</title>
<link href="https://fonts.googleapis.com/css2?family=Poppins:wght@400;500;700&display=swap" rel="stylesheet">
<style>
  :root {
    --page-bg: #ecedec;
    --card-white: #ffffff;
    --brand-yellow: #edb446;
    --brand-blue: #1e7fb8;
    --ink: #2b2a28;
    --on-yellow: #ffffff;
  }
  * { box-sizing: border-box; margin: 0; padding: 0; }
  html, body {
    width: 1067px; height: 1200px; overflow: hidden;
    background: var(--page-bg);
    font-family: "Poppins", sans-serif;
  }
  .canvas { position: relative; width: 1067px; height: 1200px; }

  .card { position: absolute; left: 200px; width: 667px; height: 357px; overflow: hidden; }

  /* Front */
  .card-front { top: 179px; background: var(--card-white); }
  .card-front .accent-band {
    position: absolute; left: 0; right: 0; bottom: 0; height: 23px;
    background: var(--brand-yellow);
  }
  .front-brand {
    position: absolute; left: 0; right: 0; top: 118px;
    display: flex; flex-direction: column; align-items: center; gap: 16px;
  }
  .brand-dot { width: 56px; height: 56px; border-radius: 50%; background: var(--brand-blue); }
  .brand-name {
    font-weight: 700; font-size: 24px; letter-spacing: 0.5px;
    color: var(--brand-blue); line-height: 1;
  }

  /* Back */
  .card-back { top: 663px; background: var(--brand-yellow); color: var(--ink); }
  .card-title {
    position: absolute; left: 35px; top: 30px;
    font-weight: 500; font-size: 21px; letter-spacing: 0.3px; line-height: 1.1;
    padding-bottom: 2px; border-bottom: 1.5px solid var(--ink);
  }
  .back-brand {
    position: absolute; right: 35px; top: 70px; width: 240px;
    display: flex; flex-direction: column; align-items: center; gap: 14px;
  }
  .back-brand .brand-dot { background: var(--on-yellow); width: 60px; height: 60px; }
  .back-brand .brand-name { color: var(--on-yellow); font-size: 20px; }

  .contact-list {
    position: absolute; left: 35px; top: 178px;
    list-style: none; font-size: 17.5px; line-height: 1.5; font-weight: 400;
  }
  .contact-item { display: flex; align-items: flex-start; margin-bottom: 4px; }
  .contact-icon { width: 16px; height: 16px; margin-top: 6px; margin-right: 16px; flex: none; }
  .contact-icon svg { width: 16px; height: 16px; display: block; }
  .phone-lines span { display: block; }
</style>
</head>
<body>
<div class="canvas">

  <section class="card card-front">
    <div class="front-brand">
      <div class="brand-dot"></div>
      <div class="brand-name">HARBORLINE AUTO</div>
    </div>
    <div class="accent-band"></div>
  </section>

  <section class="card card-back">
    <h2 class="card-title">CAR DEALER CUSTOMER SERVICE</h2>

    <div class="back-brand">
      <div class="brand-dot"></div>
      <div class="brand-name">HARBORLINE AUTO</div>
    </div>

    <ul class="contact-list">
      <li class="contact-item">
        <span class="contact-icon">
          <svg viewBox="0 0 16 16"><path d="M3.5 1.5l2.5 0.3 1 3.2-1.6 1.2c0.8 1.8 2.2 3.2 4 4l1.2-1.6 3.2 1 0.3 2.5c-0.3 1-1.3 1.7-2.3 1.6C6.5 13.2 2.8 9.5 2 4.1 1.9 3 2.6 1.9 3.5 1.5z" fill="none" stroke="currentColor" stroke-width="1.4"/></svg>
        </span>
        <span class="phone-lines"><span>(931) 555-0148</span><span>(629) 555-0173</span></span>
      </li>
      <li class="contact-item">
        <span class="contact-icon">
          <svg viewBox="0 0 16 16"><rect x="1" y="3.5" width="14" height="9" fill="currentColor"/><path d="M1.5 4l6.5 5 6.5-5" fill="none" stroke="#edb446" stroke-width="1.2"/></svg>
        </span>
        <span>harborlineautoxq@mailnest.example</span>
      </li>
      <li class="contact-item">
        <span class="contact-icon">
          <svg viewBox="0 0 16 16" fill="none" stroke="currentColor" stroke-width="1.2"><circle cx="8" cy="8" r="6.5"/><ellipse cx="8" cy="8" rx="3" ry="6.5"/><path d="M1.5 8h13M2.5 5h11M2.5 11h11"/></svg>
        </span>
        <span>www.harborlineautoxq.net</span>
      </li>
      <li class="contact-item">
        <span class="contact-icon">
          <svg viewBox="0 0 16 16" fill="none" stroke="currentColor" stroke-width="1.4"><path d="M8 12s-4-4-4-7a4 4 0 0 1 8 0c0 3-4 7-4 7z"/><circle cx="8" cy="5" r="1.4"/><path d="M2.5 15h11"/></svg>
        </span>
        <span>2874 Cresthaven Road, Shelbyville, TN 37162</span>
      </li>
    </ul>
  </section>

</div>
</body>
</html>
```